Wine Label for a Sweet Wine Called "Glimmo"

We need a wine label that will be used for both a sweet red and a sweet white wine. The very important thing to remember is the target market for these wines is: young American women who love sweet wines and they also spend a lot of their money on their hair, clothes, jewelry, nails. They LOVE Glimmo (Glimmo is a word used to describe flashy accessories, jewelry, decoration.) This label needs to be eye catching, showy, fun, glittery. Please put the brand name, "Glimmo," big, and then in smaller but still readable words underneath the label or somewhere on the label: Sweet, Sophisticated, Red (or white). (An example of what I mean is attached). To differentiate between the two color wines you can suggest color changes to differentiate between the red label and the white label but the label design itself should be the same. Ultimately, the label can be the exact same label for both white and red as long as it looks good on a white wine (a greenish/yellow wine in a clear glass bottle) and a red wine (a dark color wine in a dark bottle).

I've attached an example of the text size relationship between the word Glimmo and the words to go underneath or elsewhere on the label, but you can certainly play with this-- it is just a suggestion of the text size relationship, and definitely NOT at all mandatory that you use any of these fonts.

You can pick the size of the label but try to stay within normal wine label sizes, meaning don't go bigger than approx. 3.5 inches wide and 5 inches tall.

Target Market(s)

Young American women who love sweet wines and spend a lot of money on their hair, clothes, jewelry, nails. They love Glimmo (Glimmo is a word that means flashy accessories, jewelry, decoration)

Requirements
Must have
• It needs to be flashy, glittery, fun, eye catching, memorable
Nice to have
• It shouldn't be too too ultra feminine! The target market is strong independent women and we also have men who will buy it too.

```html
<!DOCTYPE html>
<html lang="en">
<head>
<meta charset="utf-8">
<title>Glimmo Wine Labels</title>
<link rel="stylesheet" href="https://fonts.googleapis.com/css2?family=Pinyon+Script&family=Montserrat:wght@400&display=swap">
<style>
  :root {
    --canvas: #ffffff;
    --white-frame: #6b7d2c;
    --white-band: #c5cc72;
    --white-panel-top: #c6cc72;
    --white-panel-bottom: #5f7a22;
    --white-rule: #7a8a3a;
    --white-ornament: #6f7f2e;
    --red-frame: #5c0a0c;
    --red-band: #c4c47a;
    --red-panel-top: #c95f36;
    --red-panel-bottom: #6c0a0d;
    --red-rule: #8a2a18;
    --red-ornament: #7a1a12;
    --ink-light: #ffffff;
  }
  * { margin: 0; padding: 0; box-sizing: border-box; }
  html, body {
    width: 1011px;
    height: 1200px;
    overflow: hidden;
    background: var(--canvas);
  }
  .canvas {
    position: relative;
    width: 1011px;
    height: 1200px;
  }
  .label {
    position: absolute;
    left: 102px;
    width: 298px;
    height: 427px;
  }
  .label--white { top: 117px; }
  .label--red { top: 678px; }
  .label svg { display: block; width: 100%; height: 100%; }
  .brand-name {
    font-family: "Pinyon Script", cursive;
    font-size: 46px;
    fill: var(--ink-light);
  }
  .tagline {
    font-family: "Montserrat", sans-serif;
    font-size: 6.6px;
    letter-spacing: 0.9px;
    fill: var(--ink-light);
  }
</style>
</head>
<body>
<main class="canvas">

  <section class="label label--white" aria-label="Glimmo sweet white wine label">
    <svg viewBox="0 0 250 358" xmlns="http://www.w3.org/2000/svg">
      <defs>
        <linearGradient id="panel-white" x1="0" y1="0" x2="0" y2="1">
          <stop offset="0" stop-color="var(--white-panel-top)"/>
          <stop offset="1" stop-color="var(--white-panel-bottom)"/>
        </linearGradient>
      </defs>
      <rect class="frame" x="0" y="0" width="250" height="358" rx="48" fill="var(--white-frame)"/>
      <rect class="frame-line" x="6" y="6" width="238" height="346" rx="43" fill="var(--ink-light)"/>
      <rect class="band" x="8" y="8" width="234" height="342" rx="41" fill="var(--white-band)"/>
      <rect class="panel" x="17" y="10" width="216" height="334" rx="34" fill="url(#panel-white)"/>
      <rect class="ornament" x="88" y="34" width="74" height="16" rx="4" fill="var(--white-ornament)" opacity="0.55" role="img" aria-label="Grape vine flourish ornament"/>
      <line class="rule" x1="25" y1="52" x2="225" y2="52" stroke="var(--white-rule)" stroke-width="1.4"/>
      <text class="brand-name" x="125" y="198" text-anchor="middle">Glimmo</text>
      <line class="rule" x1="25" y1="317" x2="225" y2="317" stroke="var(--ink-light)" stroke-width="0.8" opacity="0.8"/>
      <text class="tagline" x="125" y="334" text-anchor="middle">SWEET | SOPHISTICATED | WHITE</text>
    </svg>
  </section>

  <section class="label label--red" aria-label="Glimmo sweet red wine label">
    <svg viewBox="0 0 250 358" xmlns="http://www.w3.org/2000/svg">
      <defs>
        <linearGradient id="panel-red" x1="0" y1="0" x2="0" y2="1">
          <stop offset="0" stop-color="var(--red-panel-top)"/>
          <stop offset="1" stop-color="var(--red-panel-bottom)"/>
        </linearGradient>
      </defs>
      <rect class="frame" x="0" y="0" width="250" height="358" rx="48" fill="var(--red-frame)"/>
      <rect class="frame-line" x="6" y="6" width="238" height="346" rx="43" fill="var(--ink-light)"/>
      <rect class="band" x="8" y="8" width="234" height="342" rx="41" fill="var(--red-band)"/>
      <rect class="panel" x="17" y="10" width="216" height="334" rx="34" fill="url(#panel-red)"/>
      <rect class="ornament" x="88" y="34" width="74" height="16" rx="4" fill="var(--red-ornament)" opacity="0.6" role="img" aria-label="Grape vine flourish ornament"/>
      <line class="rule" x1="25" y1="52" x2="225" y2="52" stroke="var(--red-rule)" stroke-width="1.4"/>
      <text class="brand-name" x="125" y="198" text-anchor="middle">Glimmo</text>
      <line class="rule" x1="25" y1="317" x2="225" y2="317" stroke="var(--ink-light)" stroke-width="0.8" opacity="0.8"/>
      <text class="tagline" x="125" y="334" text-anchor="middle">SWEET | SOPHISTICATED | WHITE</text>
    </svg>
  </section>

</main>
</body>
</html>
```